Life Coaching Business - needs business card design with logo

I need a business card and logo design for a life coaching business I started based in Los Angeles. I offer services to clients that wish to bring more balance and overall wholeness to their lives. As of right now, the business name is "Marcus Ellery Coaching." An iidea I had for the logo was to be kind of a Yin-Yang symbol but with dolphins, as the dolphin has symbolic meaning for my business. Although I am really open to other ideas as long as it incorporates the idea of “balance,” “wholeness,” and “dolphins.”I also wanted to incorporate the color blue, maybe in the form of water, waves, or some sort of peaceful imagery.

```html
<!DOCTYPE html>
<html lang="en">
<head>
<meta charset="utf-8">
<title>Marcus Ellery Coaching – Business Card</title>
<link href="https://fonts.googleapis.com/css2?family=Open+Sans:wght@400;600&display=swap" rel="stylesheet">
<style>
  :root {
    --backdrop: #e4e4e4;
    --water-light: #d9f0f7;
    --water-mid: #9fd6e6;
    --water-deep: #5fb4cf;
    --ink: #101418;
    --name-blue: #2a4696;
    --mark: #1d3f78;
  }
  * { margin: 0; padding: 0; box-sizing: border-box; }
  html, body {
    width: 1200px;
    height: 864px;
    overflow: hidden;
    background: var(--backdrop);
    font-family: "Open Sans", sans-serif;
  }
  .canvas {
    width: 1200px;
    height: 864px;
    display: flex;
    flex-direction: column;
    align-items: center;
    justify-content: center;
    gap: 56px;
  }
  .card {
    position: relative;
    width: 560px;
    height: 320px;
    overflow: hidden;
    box-shadow: 0 2px 6px rgba(0,0,0,0.12);
  }
  .card-water {
    position: absolute;
    inset: 0;
    background:
      radial-gradient(ellipse at 70% 80%, var(--water-light) 0%, transparent 55%),
      linear-gradient(135deg, var(--water-deep) 0%, var(--water-mid) 50%, var(--water-light) 100%);
  }
  .card-content {
    position: relative;
    height: 100%;
    display: flex;
    flex-direction: column;
    align-items: center;
    text-align: center;
    color: var(--ink);
  }
  .brand-dot {
    width: 82px;
    height: 82px;
    border-radius: 50%;
    background: var(--mark);
  }
  .company {
    font-size: 25px;
    font-weight: 600;
    letter-spacing: 0.2px;
  }
  .person {
    font-size: 21px;
    color: var(--name-blue);
    margin-top: 2px;
  }
  .phone { font-size: 13px; margin-top: 8px; }
  .email { font-size: 14px; margin-top: 2px; }

  .card-front .card-content { padding-top: 46px; }
  .card-front .company { margin-top: 12px; }

  .card-back .card-content { padding-top: 92px; }
  .card-back .company { margin-top: 16px; }
</style>
</head>
<body>
<main class="canvas">
  <section class="card card-front">
    <div class="card-water" role="img" aria-label="Light blue water droplets covering the card"></div>
    <div class="card-content">
      <div class="brand-dot"></div>
      <p class="company">Marcus Ellery Coaching.</p>
      <p class="person">Daniel Harrow</p>
      <p class="phone">0214529316</p>
      <p class="email">dharrow@Coachmail.com</p>
    </div>
  </section>

  <section class="card card-back">
    <div class="card-water" role="img" aria-label="Light blue water droplets covering the card"></div>
    <div class="card-content">
      <div class="brand-dot"></div>
      <p class="company">Marcus Ellery Coaching.</p>
    </div>
  </section>
</main>
</body>
</html>
```